TA BRAMLEY BUSINESS CARD DESIGN PROJECT

We need to utilize our logo that was expertly created on PixelHarbor and now need to match this with a business card design.

```html
<!DOCTYPE html>
<html lang="en">
<head>
<meta charset="utf-8">
<title>TA BRAMLEY Business Card</title>
<link rel="stylesheet" href="https://fonts.googleapis.com/css2?family=Montserrat:wght@400;500;700&display=swap">
<style>
  :root {
    --brand-blue: #0f55a8;
    --ink: #2b2b2b;
    --card-white: #ffffff;
    --backdrop: #e3e3e0;
  }
  * { box-sizing: border-box; margin: 0; padding: 0; }
  html, body {
    width: 1200px;
    height: 801px;
    overflow: hidden;
  }
  body {
    background: var(--backdrop);
    font-family: "Montserrat", sans-serif;
    display: flex;
    align-items: center;
    justify-content: center;
    gap: 40px;
  }
  .card {
    position: relative;
    width: 540px;
    height: 309px;
    background: var(--card-white);
    border-bottom: 4px solid var(--brand-blue);
    box-shadow: 0 6px 18px rgba(0,0,0,0.12);
    overflow: hidden;
  }

  /* Contact side */
  .card--contact .side-tab {
    position: absolute;
    left: 0;
    top: 196px;
    width: 10px;
    height: 44px;
    background: var(--brand-blue);
  }
  .card--contact .details {
    position: absolute;
    left: 38px;
    top: 34px;
    color: var(--ink);
  }
  .brand-small {
    display: flex;
    align-items: center;
    gap: 8px;
    color: var(--brand-blue);
    font-weight: 700;
    font-size: 20px;
    letter-spacing: 3px;
    margin-bottom: 20px;
  }
  .brand-small .brand-dot {
    width: 14px;
    height: 14px;
    background: var(--brand-blue);
  }
  .person-name {
    color: var(--brand-blue);
    font-weight: 700;
    font-size: 16px;
    letter-spacing: 0.5px;
  }
  .person-role {
    font-size: 12px;
    margin-bottom: 14px;
  }
  .address {
    font-size: 12px;
    line-height: 1.35;
    margin-bottom: 14px;
  }
  .contact-list { list-style: none; font-size: 12px; line-height: 1.55; }
  .contact-list li { display: flex; align-items: center; gap: 7px; }
  .contact-list svg { width: 11px; height: 11px; fill: var(--brand-blue); flex: none; }

  .brand-large {
    position: absolute;
    right: 36px;
    top: 50%;
    transform: translateY(-50%);
    color: var(--brand-blue);
    font-weight: 700;
    font-size: 40px;
    line-height: 1.05;
    letter-spacing: 4px;
    text-align: right;
  }

  /* Logo side */
  .card--logo {
    display: flex;
    align-items: center;
    justify-content: center;
  }
  .brand-center {
    display: flex;
    align-items: center;
    gap: 16px;
    color: var(--brand-blue);
    font-weight: 700;
    font-size: 48px;
    letter-spacing: 8px;
  }
  .brand-center .brand-dot {
    width: 30px;
    height: 30px;
    background: var(--brand-blue);
  }
</style>
</head>
<body>

  <section class="card card--contact" aria-label="Business card contact side">
    <div class="side-tab"></div>
    <div class="details">
      <div class="brand-small"><span class="brand-dot"></span>TA BRAMLEY</div>
      <p class="person-name">NORA HALE</p>
      <p class="person-role">Managing Director</p>
      <p class="address">Your address, City<br>State, Zip 1234</p>
      <ul class="contact-list">
        <li>
          <svg viewBox="0 0 24 24"><path d="M6.6 10.8a15 15 0 0 0 6.6 6.6l2.2-2.2c.3-.3.7-.4 1-.2 1.1.4 2.3.6 3.6.6.6 0 1 .4 1 1V20c0 .6-.4 1-1 1A17 17 0 0 1 3 4c0-.6.4-1 1-1h3.5c.6 0 1 .4 1 1 0 1.3.2 2.5.6 3.6.1.3 0 .7-.2 1z"/></svg>
          123 456 789
        </li>
        <li>
          <svg viewBox="0 0 24 24"><path d="M6 2h9l3 3v5H6zM3 11h18v9H3zm3 2v2h3v-2zm5 0v2h3v-2zm5 0v2h3v-2zM6 16v2h3v-2zm5 0v2h3v-2z"/></svg>
          123 456 789
        </li>
        <li>
          <svg viewBox="0 0 24 24"><path d="M2 5h20v14H2zm2 2v.5l8 5 8-5V7z"/></svg>
          info@yourgmail.com
        </li>
        <li>
          <svg viewBox="0 0 24 24"><path d="M12 2a10 10 0 1 0 0 20 10 10 0 0 0 0-20zm6.9 6h-3a15 15 0 0 0-1.3-4A8 8 0 0 1 18.9 8zM12 4c.8 1.2 1.5 2.5 1.9 4h-3.8c.4-1.5 1.1-2.8 1.9-4zM4.3 14a8 8 0 0 1 0-4h3.4a16 16 0 0 0 0 4zm.8 2h3a15 15 0 0 0 1.3 4A8 8 0 0 1 5.1 16zm3-8h-3a8 8 0 0 1 4.3-4A15 15 0 0 0 8.1 8zM12 20c-.8-1.2-1.5-2.5-1.9-4h3.8c-.4 1.5-1.1 2.8-1.9 4zm2.3-6H9.7a14 14 0 0 1 0-4h4.6a14 14 0 0 1 0 4zm.3 6a15 15 0 0 0 1.3-4h3a8 8 0 0 1-4.3 4zm1.7-6a16 16 0 0 0 0-4h3.4a8 8 0 0 1 0 4z"/></svg>
          www.yourwebsite.com
        </li>
      </ul>
    </div>
    <div class="brand-large">TA<br>BRAMLEY</div>
  </section>

  <section class="card card--logo" aria-label="Business card logo side">
    <div class="brand-center"><span class="brand-dot"></span>TA BRAMLEY</div>
  </section>

</body>
</html>
```